Brookvane Consulting Business Card Design

Business Card Design for Brookvane Consulting. Brookvane Consulting is a boutique consultancy based in Atlanta, GA., that specializes in marketing strategy, organization planning, and leadership development. We provide solutions for small businesses and startups as well as Vantage 300 companies.

http://brookvaneconsulting.com/

Target Market(s)

We provide solutions for small businesses and startups as well as Vantage 300 companies.

Industry/Entity Type

Consulting

Contact Information for Business Card

Two sided business card with priority on contact information, logo, tag line (Guidance to plan more, lead more, achieve more)

Colors

Designer to choose colors to be used in the design.

Requirements
Must have
• contact information, logo, tag line (Guidance to plan more, lead more, achieve more)
• Simple no over communication.
Nice to have
• I would like to see different placements of logo and creative use of both sides of the card
Should not have
• Do not put too much information on the card.

```html
<!DOCTYPE html>
<html lang="en">
<head>
<meta charset="utf-8">
<title>Brookvane Consulting – Business Card</title>
<link rel="stylesheet" href="https://fonts.googleapis.com/css2?family=Mulish:wght@400;600;700&family=Lora:wght@400&display=swap">
<style>
  :root {
    --page: #e9e7e3;
    --card: #040404;
    --band: #111213;
    --pattern-dark: #1a1b1d;
    --pattern-mid: #2c2e31;
    --ink: #ffffff;
    --ink-soft: #d6d6d6;
    --rule: #f2f2f2;
  }
  * { box-sizing: border-box; margin: 0; padding: 0; }
  html, body { width: 1200px; height: 900px; overflow: hidden; }
  body {
    background: var(--page);
    font-family: "Mulish", Arial, sans-serif;
    color: var(--ink);
    display: flex;
    flex-direction: column;
    align-items: center;
    justify-content: center;
    gap: 40px;
  }
  .card {
    position: relative;
    width: 700px;
    height: 400px;
    background: var(--card);
    overflow: hidden;
    box-shadow: 0 6px 18px rgba(0,0,0,.25);
  }

  /* Contact side */
  .contact-band {
    position: absolute;
    left: 0; right: 0; bottom: 0;
    height: 150px;
    background: var(--band);
    border-top: 3px solid var(--rule);
  }
  .contact-band .texture {
    position: absolute;
    right: 0; top: 0; bottom: 0;
    width: 420px;
    background: radial-gradient(ellipse at 80% 40%, var(--pattern-mid) 0%, var(--pattern-dark) 45%, transparent 75%);
    opacity: .8;
  }
  .contact-side .brand {
    position: absolute;
    left: 54px;
    bottom: 166px;
  }
  .brand-name {
    font-family: "Mulish", Arial, sans-serif;
    font-weight: 700;
    font-size: 34px;
    letter-spacing: .5px;
    line-height: 1.1;
    color: var(--ink);
    white-space: nowrap;
  }
  .brand-name .dot {
    display: inline-block;
    width: 8px; height: 8px;
    background: var(--ink);
    border-radius: 50%;
    margin-left: 6px;
    vertical-align: middle;
  }
  .contact-side .tagline {
    font-size: 15px;
    margin-top: 6px;
    color: var(--ink);
  }
  .contact-side .site {
    font-size: 11px;
    letter-spacing: 1.5px;
    text-transform: uppercase;
    color: var(--ink-soft);
    margin-top: 4px;
  }
  .contact-list {
    position: absolute;
    left: 54px;
    bottom: 24px;
    list-style: none;
    display: flex;
    flex-direction: column;
    gap: 10px;
  }
  .contact-list li {
    display: flex;
    align-items: center;
    gap: 16px;
    font-size: 13px;
    letter-spacing: 1.8px;
    text-transform: uppercase;
    color: var(--ink-soft);
    white-space: nowrap;
  }
  .contact-list svg { width: 20px; height: 20px; flex: none; }

  /* Front side */
  .front-side .edge {
    position: absolute;
    top: -40px; bottom: -40px;
    width: 260px;
    border-radius: 50%;
  }
  .front-side .edge-left {
    left: -150px;
    background: radial-gradient(ellipse at 70% 50%, var(--pattern-mid) 0%, var(--pattern-dark) 50%, transparent 78%);
  }
  .front-side .edge-right {
    right: -150px;
    background: radial-gradient(ellipse at 30% 50%, var(--pattern-mid) 0%, var(--pattern-dark) 50%, transparent 78%);
  }
  .front-side .centre {
    position: absolute;
    inset: 0;
    display: flex;
    flex-direction: column;
    align-items: center;
    justify-content: center;
    text-align: center;
  }
  .front-side .tagline {
    font-family: "Lora", Georgia, serif;
    font-size: 19px;
    line-height: 1.2;
    margin-top: 10px;
    color: var(--ink);
  }
</style>
</head>
<body>

  <section class="card contact-side">
    <div class="brand">
      <div class="brand-name">Brookvane Consulting<span class="dot"></span></div>
      <p class="tagline">Guidance to plan more, lead more, achieve more</p>
      <p class="site">brookvaneconsulting.com</p>
    </div>
    <div class="contact-band">
      <div class="texture" role="img" aria-label="Dark faceted swirl texture"></div>
    </div>
    <ul class="contact-list">
      <li>
        <svg viewBox="0 0 20 20" aria-hidden="true"><rect x="2" y="5" width="16" height="10" fill="none" stroke="#fff" stroke-width="1.6"/><path d="M2 5l8 6 8-6" fill="none" stroke="#fff" stroke-width="1.6"/></svg>
        dara@brookvaneconsulting.com
      </li>
      <li>
        <svg viewBox="0 0 20 20" aria-hidden="true"><path d="M5 3l3 3-2 2c1 2 3 4 5 5l2-2 3 3-2 3C8 16 4 12 3 5z" fill="#fff"/></svg>
        555-302-4417
      </li>
      <li>
        <svg viewBox="0 0 20 20" aria-hidden="true"><g fill="none" stroke="#fff" stroke-width="1.4"><circle cx="10" cy="10" r="7.5"/><ellipse cx="10" cy="10" rx="3.2" ry="7.5"/><path d="M2.5 10h15M4 6h12M4 14h12"/></g></svg>
        http://brookvaneconsulting.com/home.html
      </li>
    </ul>
  </section>

  <section class="card front-side">
    <div class="edge edge-left" role="img" aria-label="Dark faceted swirl texture along the left edge"></div>
    <div class="edge edge-right" role="img" aria-label="Dark faceted swirl texture along the right edge"></div>
    <div class="centre">
      <div class="brand-name">Brookvane Consulting<span class="dot"></span></div>
      <p class="tagline">Guidance to plan more,<br>lead more, achieve more</p>
    </div>
  </section>

</body>
</html>
```